Brightway Haus Inc. Business Card Design

Brightway Haus Inc. is in search of a great clean design for our business cards!

Looking to incorporate our full logo and watermark on side one (however, I am open to having the text and watermark separated within the design.)

On side two, I am looking to have contact information (Name, Position, Phone #, Email, Website (www.thebrightwayhaus.ca). Can have the logo and/or watermark as part of the design if applicable.

Please add tagline "Where Shine Counts" on either side 1 or 2. This tagline can be in a sans serif, serif or cursive font as long as it compliments overall design. Capitalization can be title or sentence case depending on how it fits within the design.

Get creative!! Looking for a clean, crisp, premium design! Looking for a glossy card finish with spot UV features when printed. Cards will also be printed with rounded corners. Standard dimensions (3.5 x 2).

Target Market(s)

B2B - primary clients are business owners or property management corporations. (residential jobs are few and far between)

Industry/Entity Type

Business

Contact Information for Business Card

- clean, crisp design
- double sided
- spot UV accents and glossy finish upon printing
- standard business card size (3.5 x 2) with rounded corners
- please see project description for requirements per side

Font styles to use
Sans Serif

Requirements
Must have
• - adequate bleeds with print ready files
• - cohesive design elements between side 1 & 2
• - spot UV elements (can be on both sides or just one, use your discretion)
• - colour pallet should match the logo file provided
• - incorporate tagline "where shine counts" (this tagline can be in a serif or sans serif font as long as it is complimentary to the overall design.
Nice to have
• - Premium elements with a clean design
Should not have
• - Please omit cartoon or whimsical like designs, think premium.
• - Colours should not stray from the pallet of the provided logo.

```html
<!DOCTYPE html>
<html lang="en">
<head>
<meta charset="utf-8">
<title>Brightway Haus Inc. Business Card</title>
<link href="https://fonts.googleapis.com/css2?family=Roboto:ital,wght@0,400;0,500;0,700;1,400&display=swap" rel="stylesheet">
<style>
  :root {
    --stage: #2e2e30;
    --card-light: #f4f4f4;
    --teal: #12b0b2;
    --navy: #1d2650;
    --ink: #4a4a4a;
    --rule: #9a9a9a;
    --white: #ffffff;
  }
  * { margin: 0; padding: 0; box-sizing: border-box; }
  html, body { width: 1200px; height: 960px; overflow: hidden; }
  body {
    position: relative;
    background: var(--stage);
    font-family: "Roboto", Arial, sans-serif;
  }
  .card {
    position: absolute;
    width: 600px;
    height: 342px;
    border-radius: 22px;
    overflow: hidden;
  }
  .card-front { left: 314px; top: 114px; background: var(--card-light); }
  .card-back { left: 311px; top: 472px; background: var(--teal); }

  .wordmark {
    position: absolute;
    display: flex;
    align-items: center;
    gap: 12px;
    font-weight: 700;
    font-size: 31px;
    letter-spacing: 0.5px;
    white-space: nowrap;
  }
  .wordmark-mark { width: 30px; height: 30px; }
  .card-front .wordmark { left: 46px; top: 52px; color: var(--navy); }
  .card-front .wordmark-mark { background: var(--teal); }
  .card-back .wordmark {
    left: 0; right: 0; top: 150px;
    justify-content: center;
    color: var(--white);
  }
  .card-back .wordmark-mark { background: var(--white); }

  .accent-bar {
    position: absolute;
    left: 0; top: 146px;
    width: 12px; height: 37px;
    background: var(--teal);
  }
  .person-name {
    position: absolute;
    left: 45px; top: 144px;
    font-size: 20px; font-weight: 500;
    color: var(--teal);
  }
  .person-role {
    position: absolute;
    left: 45px; top: 169px;
    font-size: 15px; font-weight: 500;
    color: var(--navy);
  }
  .contact-list {
    position: absolute;
    left: 47px; top: 212px;
    list-style: none;
  }
  .contact-list li {
    display: flex;
    align-items: center;
    gap: 9px;
    height: 19.2px;
    font-size: 14px;
    color: var(--ink);
    white-space: nowrap;
  }
  .contact-icon { width: 13px; height: 13px; fill: var(--teal); flex: none; }
  .address {
    position: absolute;
    left: 244px; top: 270px;
    padding-left: 16px;
    border-left: 1.5px solid var(--rule);
    font-size: 14px;
    font-style: normal;
    line-height: 19px;
    color: var(--ink);
    white-space: nowrap;
  }

  .tagline {
    position: absolute;
    left: 0; right: 0; top: 276px;
    display: flex;
    align-items: center;
    justify-content: center;
    gap: 6px;
    color: var(--white);
    font-style: italic;
    font-size: 18px;
  }
  .tagline-rule {
    width: 108px; height: 1px;
    background: linear-gradient(to right, rgba(255,255,255,0), rgba(255,255,255,0.8));
  }
  .tagline-rule.right {
    width: 96px;
    background: linear-gradient(to left, rgba(255,255,255,0), rgba(255,255,255,0.8));
  }
</style>
</head>
<body>
  <section class="card card-front" aria-label="Business card, contact side">
    <div class="wordmark"><span class="wordmark-mark"></span>BRIGHTWAY HAUS INC.</div>
    <div class="accent-bar"></div>
    <h1 class="person-name">DANIEL REYES</h1>
    <p class="person-role">CEO/FOUNDER</p>
    <ul class="contact-list">
      <li><svg class="contact-icon" viewBox="0 0 24 24"><path d="M6.6 10.8a15.1 15.1 0 0 0 6.6 6.6l2.2-2.2c.3-.3.7-.4 1-.2 1.1.4 2.3.6 3.6.6.6 0 1 .4 1 1V20c0 .6-.4 1-1 1A17 17 0 0 1 3 4c0-.6.4-1 1-1h3.5c.6 0 1 .4 1 1 0 1.3.2 2.5.6 3.6.1.3 0 .7-.2 1z"/></svg>604 218 3057</li>
      <li><svg class="contact-icon" viewBox="0 0 24 24"><path d="M7 1h10a2 2 0 0 1 2 2v18a2 2 0 0 1-2 2H7a2 2 0 0 1-2-2V3a2 2 0 0 1 2-2zm0 3v14h10V4zm5 15.5a1.2 1.2 0 1 0 0 2.4 1.2 1.2 0 0 0 0-2.4z"/></svg>604 771 4826</li>
      <li><svg class="contact-icon" viewBox="0 0 24 24"><path d="M6 2h12v6H6zM3 9h18a2 2 0 0 1 2 2v7h-4v4H5v-4H1v-7a2 2 0 0 1 2-2zm4 7v4h10v-4z"/></svg>604 390 6152</li>
      <li><svg class="contact-icon" viewBox="0 0 24 24"><path d="M2 5h20v14H2zm2 2v.5l8 5 8-5V7z"/></svg>hi@brightwayhaus.ca</li>
      <li><svg class="contact-icon" viewBox="0 0 24 24"><circle cx="12" cy="12" r="10"/></svg>www.thebrightwayhaus.ca</li>
    </ul>
    <address class="address">1420 Harbour Ridge Way<br>Vancouver, BC V6B 2K9</address>
  </section>

  <section class="card card-back" aria-label="Business card, brand side">
    <div class="wordmark"><span class="wordmark-mark"></span>BRIGHTWAY HAUS INC.</div>
    <p class="tagline"><span class="tagline-rule"></span>Where Shine Counts<span class="tagline-rule right"></span></p>
  </section>
</body>
</html>
```